New iOS App design for Boston Startup

We are looking for a new app design for our iPhone app. The current app's design feels outdated and we like to add lots of new functionality and a new navigation as well. A complete overhaul therefore!
We want you to design 5 screens that will have changed the most. The complete wireframes of these 5 pages are attached in the requirements document.
Once the winning design is selected we will award the winner with the designing all other screens (40-50 screens based on the same design). This will be a separate project worth $1000. The winning designer can get more follow up work if both sides are happy about the cooperation.
We will give feedback as soon as the first screen has been uploaded for review. Final decision will be made only after all 5 screens are finished.
We hope you give it your best!
Note: will only communicate through PixelHarbor (no skype),
Updates
Reason: Want to give designers a chance to submit their designs as I understand from some, the deadline is too close.
I have raised the award and introduced a 2nd price as well to make it worth your time. I hope you give it your best shot.
Reason: A few of you have asked for an extension of the deadline as time is running out. I will extend by one day. Tell me if you need more.
Industry/Entity Type
Startup
Requirements
Must have
- At least 1 screen before we can give you feedback.
Nice to have
- multiple options of 1 screen to get to a desirable design

```html
<!DOCTYPE html>
<html lang="en">
<head>
<meta charset="utf-8">
<title>Study Dashboard – Home Screen</title>
<link href="https://fonts.googleapis.com/css2?family=Open+Sans:wght@400;600;700&display=swap" rel="stylesheet">
<style>
  :root {
    --canvas: #f1f2f4;
    --brand-blue: #2889d3;
    --brand-blue-dark: #1f74b8;
    --divider: rgba(255,255,255,0.55);
    --white: #ffffff;
    --ink: #222222;
    --ink-soft: #555555;
    --gain: #b6f03c;
    --loss: #ff4a4a;
    --button-dark: #5a5a5a;
    --tab-bg: #f7f7f7;
    --tab-line: #dddddd;
    --dot-off: rgba(255,255,255,0.45);
  }
  * { box-sizing: border-box; margin: 0; padding: 0; }
  html, body {
    width: 1200px; height: 1041px; overflow: hidden;
    background: var(--canvas);
    font-family: "Open Sans", Arial, sans-serif;
  }
  .screen {
    position: absolute; left: 360px; top: 94px;
    width: 480px; height: 852px;
    background: var(--white);
    display: flex; flex-direction: column;
    box-shadow: 0 10px 40px rgba(0,0,0,0.08);
  }
  .dashboard { background: var(--brand-blue); color: var(--white); }
  .status-bar {
    height: 30px; display: flex; align-items: center; justify-content: space-between;
    padding: 0 12px; font-size: 12px; font-weight: 600;
  }
  .status-bar .signal { letter-spacing: 1px; }
  .title-bar {
    height: 54px; display: flex; align-items: center; justify-content: center; position: relative;
    font-size: 19px; font-weight: 600;
  }
  .title-bar .menu { position: absolute; left: 18px; top: 16px; }
  .score-panel { position: relative; padding: 8px 40px 0; }
  .score-line {
    display: flex; align-items: baseline; justify-content: center; gap: 14px;
  }
  .score-label { font-size: 34px; font-weight: 400; }
  .score-value { font-size: 76px; font-weight: 700; line-height: 1; }
  .score-delta { font-size: 28px; color: var(--loss); font-weight: 600; }
  .carousel-arrow { position: absolute; top: 60px; }
  .carousel-arrow.prev { left: 12px; }
  .carousel-arrow.next { right: 12px; }
  .stats {
    display: flex; justify-content: space-between; padding: 14px 0 16px;
  }
  .stat { flex: 1; text-align: center; border-right: 1px solid var(--divider); }
  .stat:last-child { border-right: none; }
  .stat-value { font-size: 16px; font-weight: 700; }
  .stat-value .num { color: var(--gain); }
  .stat-label { font-size: 13px; }
  .tiles { display: flex; border-top: 2px solid var(--white); }
  .tile {
    flex: 1; height: 120px; border-right: 2px solid var(--white);
    display: flex; flex-direction: column; align-items: center; justify-content: center;
    gap: 8px; font-size: 15px; text-align: center; position: relative; line-height: 1.15;
  }
  .tile:last-child { border-right: none; }
  .tile .chev { position: absolute; right: 10px; top: 52px; }
  .pager { display: flex; justify-content: center; gap: 8px; padding: 10px 0; background: var(--brand-blue-dark); }
  .pager span { width: 8px; height: 8px; border-radius: 50%; background: var(--white); }
  .pager span.off { background: var(--dot-off); }
  .up-next { flex: 1; display: flex; flex-direction: column; align-items: center; padding-top: 44px; }
  .up-next-label { font-size: 20px; font-weight: 600; color: var(--ink); margin-bottom: 14px; }
  .up-next-button {
    width: 360px; height: 58px; border-radius: 6px; background: var(--button-dark);
    color: var(--white); font-size: 21px; display: flex; align-items: center; justify-content: center;
  }
  .tab-bar {
    height: 86px; display: flex; background: var(--tab-bg); border-top: 1px solid var(--tab-line);
  }
  .tab {
    flex: 1; display: flex; flex-direction: column; align-items: center; justify-content: center;
    gap: 6px; font-size: 12px; font-weight: 600; color: var(--ink-soft);
  }
</style>
</head>
<body>
<main class="screen">
  <section class="dashboard">
    <div class="status-bar">
      <span class="signal">●●● VERA</span>
      <span>4:21 PM</span>
      <span>100%</span>
    </div>
    <header class="title-bar">
      <svg class="menu" width="26" height="20" viewBox="0 0 26 20"><g fill="#fff"><rect width="26" height="3"/><rect y="8" width="26" height="3"/><rect y="16" width="26" height="3"/></g></svg>
      <span>Welcome back, Noam</span>
    </header>
    <div class="score-panel">
      <svg class="carousel-arrow prev" width="14" height="24" viewBox="0 0 14 24"><path d="M12 2 2 12l10 10" fill="none" stroke="#fff" stroke-width="3"/></svg>
      <svg class="carousel-arrow next" width="14" height="24" viewBox="0 0 14 24"><path d="M2 2l10 10L2 22" fill="none" stroke="#fff" stroke-width="3"/></svg>
      <div class="score-line">
        <span class="score-label">Score</span>
        <span class="score-value">650</span>
        <span class="score-delta">-18</span>
      </div>
      <div class="stats">
        <div class="stat"><div class="stat-value"><span class="num">34%</span> +4</div><div class="stat-label">Completion</div></div>
        <div class="stat"><div class="stat-value"><span class="num">20</span> +3</div><div class="stat-label">Sessions</div></div>
        <div class="stat"><div class="stat-value"><span class="num">18</span> +10</div><div class="stat-label">This week</div></div>
      </div>
    </div>
    <nav class="tiles">
      <div class="tile">
        <svg width="34" height="24" viewBox="0 0 34 24"><g fill="none" stroke="#fff" stroke-width="2"><path d="M2 22h30"/><path d="M6 22v-8M12 22V10M18 22v-6M24 22V8"/><path d="M4 10 12 4l8 6 10-8"/></g></svg>
        <span>Analytics</span>
        <svg class="chev" width="8" height="14" viewBox="0 0 8 14"><path d="M1 1l6 6-6 6" fill="none" stroke="#fff" stroke-width="2"/></svg>
      </div>
      <div class="tile">
        <svg width="30" height="24" viewBox="0 0 30 24"><g fill="none" stroke="#fff" stroke-width="2"><path d="M2 3h11l2 2 2-2h11v18H17l-2 2-2-2H2z"/><path d="M15 5v16"/></g></svg>
        <span>Course<br>Overview</span>
        <svg class="chev" width="8" height="14" viewBox="0 0 8 14"><path d="M1 1l6 6-6 6" fill="none" stroke="#fff" stroke-width="2"/></svg>
      </div>
      <div class="tile">
        <svg width="28" height="26" viewBox="0 0 28 26"><g fill="none" stroke="#fff" stroke-width="2"><rect x="2" y="5" width="24" height="19" rx="2"/><path d="M2 11h24M8 2v6M20 2v6"/><circle cx="18" cy="18" r="3"/></g></svg>
        <span>Days Until<br>Test 33</span>
        <svg class="chev" width="8" height="14" viewBox="0 0 8 14"><path d="M1 1l6 6-6 6" fill="none" stroke="#fff" stroke-width="2"/></svg>
      </div>
    </nav>
    <div class="pager"><span></span><span class="off"></span><span class="off"></span><span class="off"></span></div>
  </section>

  <section class="up-next">
    <h2 class="up-next-label">Up Next:</h2>
    <div class="up-next-button">Sentence Correction Lesson 4</div>
  </section>

  <nav class="tab-bar">
    <div class="tab">
      <svg width="28" height="24" viewBox="0 0 28 24"><path d="M14 2 2 12h4v10h6v-6h4v6h6V12h4z" fill="#666"/></svg>
      <span>Home</span>
    </div>
    <div class="tab">
      <svg width="30" height="24" viewBox="0 0 30 24"><g fill="none" stroke="#666" stroke-width="2"><path d="M2 3h11l2 2 2-2h11v18H17l-2 2-2-2H2z"/><path d="M15 5v16"/></g></svg>
      <span>Theory</span>
    </div>
    <div class="tab">
      <svg width="30" height="24" viewBox="0 0 30 24"><g fill="var(--brand-blue)"><rect x="2" y="10" width="12" height="12"/><rect x="9" y="6" width="12" height="12" opacity=".8"/><rect x="16" y="2" width="12" height="12" opacity=".65"/></g></svg>
      <span>Practice</span>
    </div>
    <div class="tab">
      <svg width="32" height="24" viewBox="0 0 32 24"><path d="M8 4h16a7 7 0 0 1 7 8l-1 6a4 4 0 0 1-7 1l-2-3H11l-2 3a4 4 0 0 1-7-1l-1-6a7 7 0 0 1 7-8z" fill="#666"/><g fill="#fff"><rect x="7" y="10" width="6" height="2"/><rect x="9" y="8" width="2" height="6"/><circle cx="23" cy="9" r="1.3"/><circle cx="23" cy="13" r="1.3"/></g></svg>
      <span>Games</span>
    </div>
    <div class="tab">
      <svg width="26" height="26" viewBox="0 0 26 26"><circle cx="13" cy="13" r="12" fill="#666"/><path d="M7 13l4 4 8-8" fill="none" stroke="#fff" stroke-width="3"/></svg>
      <span>Test</span>
    </div>
  </nav>
</main>
</body>
</html>
```